Kelvara Pools

Luxury pool designer builder brochure

Company name is "Kelvara"
Tag line is "Pools for the Mind Body & Soul"
Maybe integrate "Luxury Urban Lifestyle"

Target Market(s)

30 to 65 income of 200000.00 plus Affluent, high end life style
Luxury living

Industry/Entity Type

It Company

Font styles to use
Serif

Colors
000000

Requirements
Must have
• NOTE:
• Please remove the "Aquatic environments for the under the logo.
• I want a black background with a very contemporary feel.
• This is a luxury lifestyle product.

```html
<!DOCTYPE html>
<html lang="en">
<head>
<meta charset="utf-8">
<title>Kelvara Pools — Brochure</title>
<link rel="stylesheet" href="https://fonts.googleapis.com/css2?family=Bodoni+Moda:opsz,wght@6..96,400;6..96,500&display=swap">
<style>
  :root {
    --ink: #000000;
    --paper: #ffffff;
    --backdrop: #dedede;
    --band-grey: #e6e6e6;
    --text-light: #f4f4f4;
    --text-dark: #1a1a1a;
    --muted: #8a8a8a;
  }
  * { box-sizing: border-box; margin: 0; padding: 0; }
  html, body {
    width: 1200px; height: 849px; overflow: hidden;
    background: var(--backdrop);
    font-family: "Bodoni Moda", "Didot", serif;
  }
  .stage {
    width: 1200px; height: 849px;
    display: flex; align-items: center; justify-content: center; gap: 40px;
  }
  .spread {
    width: 540px; height: 382px;
    display: flex; position: relative;
    box-shadow: 0 10px 28px rgba(0,0,0,0.18);
  }
  .page { width: 270px; height: 382px; position: relative; overflow: hidden; }

  /* Outer spread */
  .page--back, .page--front { background: var(--ink); }
  .page--back { border-right: 1px solid #161616; }
  .address {
    position: absolute; left: 36px; bottom: 48px;
    font-size: 6px; letter-spacing: 0.04em; color: var(--muted);
  }
  .tagline {
    position: absolute; right: 30px; top: 96px;
    text-align: right; color: var(--text-light);
    font-size: 15px; line-height: 1.15; font-weight: 400;
  }
  .brand-name {
    position: absolute; right: 26px; bottom: 26px;
    font-size: 9px; letter-spacing: 0.12em; color: var(--text-light);
  }

  /* Inner spread */
  .spread--inner { background: var(--paper); }
  .inner-photos {
    position: absolute; left: 0; top: 0; width: 540px; height: 290px;
    display: flex;
  }
  .photo-hero {
    width: 350px; height: 290px;
    background: linear-gradient(160deg, #7d8794 0%, #6a5a4b 35%, #c7783b 48%, #2f5d78 70%, #8c8a84 100%);
  }
  .photo-column { width: 190px; display: flex; flex-direction: column; gap: 3px; padding-left: 3px; background: var(--paper); }
  .photo-small { flex: 1; }
  .photo-small--dusk { background: linear-gradient(170deg, #8f9aa8 0%, #b89a7c 55%, #5c6f66 100%); }
  .photo-small--deck { background: linear-gradient(170deg, #7b8f97 0%, #c56a3c 45%, #8a6f5a 100%); }
  .photo-small--pool { background: linear-gradient(170deg, #6d7a6c 0%, #c9a27a 40%, #2f6f9a 100%); }
  .inner-band {
    position: absolute; left: 0; bottom: 0; width: 540px; height: 92px; display: flex;
  }
  .band-left { width: 350px; background: var(--band-grey); }
  .band-right {
    width: 190px; background: var(--paper);
    display: flex; align-items: center; justify-content: flex-end; padding-right: 20px;
  }
  .headline {
    text-align: right; color: var(--text-dark);
    font-size: 13px; line-height: 1.2; font-weight: 400;
  }
  .fold {
    position: absolute; left: 270px; top: 0; width: 1px; height: 382px;
    background: rgba(0,0,0,0.08);
  }
</style>
</head>
<body>
  <main class="stage">
    <section class="spread spread--outer" aria-label="Brochure outer spread">
      <div class="page page--back">
        <p class="address">address</p>
      </div>
      <div class="page page--front">
        <h1 class="tagline">Pools for the Mind<br>Body &amp; Soul</h1>
        <p class="brand-name">Kelvara</p>
      </div>
    </section>

    <section class="spread spread--inner" aria-label="Brochure inner spread">
      <div class="inner-photos">
        <div class="photo-hero" role="img" aria-label="Photo of a luxury infinity pool with a stone fire bowl beside a lit villa at dusk"></div>
        <div class="photo-column">
          <div class="photo-small photo-small--dusk" role="img" aria-label="Photo of a villa and pool under a dusk sky"></div>
          <div class="photo-small photo-small--deck" role="img" aria-label="Photo of a pool deck with fire features and a lit house"></div>
          <div class="photo-small photo-small--pool" role="img" aria-label="Photo of a blue pool with garden landscaping at evening"></div>
        </div>
      </div>
      <div class="inner-band">
        <div class="band-left"></div>
        <div class="band-right">
          <h2 class="headline">Discover Luxury Urban<br>Lifestyle</h2>
        </div>
      </div>
      <div class="fold"></div>
    </section>
  </main>
</body>
</html>
```